Useable Postcard Gift for Artistic Convention Use

Useable Postcard Gift Conference Use, search for web designers
Name of the Company is: Verdancy Harbor
I have an image that I would like to use for the front of the card
along with a by line which says "Let Each Step Light the Road Ahead"
Regarding image, i am good to leave the black behind.... should the designer choose. I also have a black and white image to use as well if someone needs it.

Design Target Market: State of the Art, Hip, Elegant, Conscious

This card will be used at a state of the art tech Quorvel Summit in Los Angeles. We want to hand it out to those we are interested in continuing relationship with for the purpose of building a website that is comprehensive. We are looking for designers and tech builders for the site.

This is a service business. I would like to have 3 names and titles on the back of the card and a small paragraph of copy. I like the beauty of the postcard i have saved on my account. I like Copper Gothic, thin lettering and Amazone or Caligraphy where it fits.... if it fits.

I want the card to communicate interest in Verdancy Harbor as a state of the art web community that services those progressive professionals who are interested in personal balance and who want to purchase products that are essential to a healthful life.
Updates

Project Deadline Extended
Reason: The deadline is extended through tomorrow due to the need to complete a design. Please continue support

Target Market(s)

High profile clients for coaching, web designers and web technicians for elaborate website build.

Industry/Entity Type

Progressive

Font styles to use
Serif
Script

Colors
00a88f
0555a3
6b449b
ffc214
9bcb3b
f37022

Requirements
Nice to have
• This was supposed to be the must have feature but it wouldn't return there so-----
We want the card to be elegant and definitely a useable postcard.

```html
<!DOCTYPE html>
<html lang="en">
<head>
<meta charset="utf-8">
<title>Verdancy Harbor – Postcard Back</title>
<link rel="stylesheet" href="https://fonts.googleapis.com/css2?family=Cinzel:wght@400;500&family=Petit+Formal+Script&family=Arimo&display=swap">
<style>
  :root {
    --page: #ffffff;
    --band: #6e6e6e;
    --panel-top: #ffffff;
    --panel-bottom: #d2d2d2;
    --ink: #1a1a1a;
    --divider: #000000;
    --rule: #7a7a7a;
    --stamp-border: #4a4a4a;
    --plate: #ffffff;
  }
  * { margin: 0; padding: 0; box-sizing: border-box; }
  html, body { width: 1200px; height: 923px; overflow: hidden; background: var(--page); }
  .postcard { position: relative; width: 1200px; height: 923px; background: var(--page); }

  .panel-shape { position: absolute; left: 0; top: 0; }

  .brand {
    position: absolute; top: 18px; right: 660px;
    font-family: "Cinzel", serif; font-size: 40px; font-weight: 400;
    color: #ffffff; letter-spacing: 1px; white-space: nowrap;
  }

  .name-plate {
    position: absolute; width: 366px; height: 66px;
    background: var(--plate);
    border-left: 2px solid #b8b6a6; border-right: 2px solid #b8b6a6;
    box-shadow: 0 10px 12px -6px rgba(0,0,0,0.28);
    display: flex; align-items: center;
    font-family: "Cinzel", serif; font-size: 35px; color: var(--ink);
  }
  .name-plate--1 { left: 175px; top: 98px; padding-left: 100px; }
  .name-plate--2 { left: 125px; top: 191px; padding-left: 100px; }
  .name-plate--3 { left: 45px;  top: 284px; padding-left: 100px; }

  .about {
    position: absolute; left: 44px; top: 378px; width: 492px;
    font-family: "Petit Formal Script", cursive; font-size: 22px;
    line-height: 38.5px; color: var(--ink); text-align: justify;
  }
  .about p { text-indent: 78px; }

  .divider {
    position: absolute; left: 572px; top: 0; width: 6px; height: 743px;
    background: var(--divider);
  }

  .stamp-box {
    position: absolute; left: 975px; top: 75px; width: 140px; height: 140px;
    border: 1.5px solid var(--stamp-border);
    display: flex; align-items: center; justify-content: center; text-align: center;
    font-family: "Arimo", sans-serif; font-size: 23px; line-height: 29px; color: #111;
  }

  .address-line {
    position: absolute; left: 695px; width: 406px; height: 2px; background: var(--rule);
  }
  .address-line--1 { top: 440px; }
  .address-line--2 { top: 511px; }
  .address-line--3 { top: 582px; }
  .address-line--4 { top: 653px; }
</style>
</head>
<body>
<main class="postcard">
  <svg class="panel-shape" width="575" height="790" viewBox="0 0 575 790" aria-hidden="true">
    <defs>
      <linearGradient id="panelFade" x1="0" y1="0" x2="0" y2="1">
        <stop offset="0" stop-color="var(--panel-top)"/>
        <stop offset="1" stop-color="var(--panel-bottom)"/>
      </linearGradient>
    </defs>
    <path d="M0 80 H572 V740 H190 C150 740 145 780 105 780 H0 Z" fill="url(#panelFade)"/>
    <path d="M0 0 H572 V80 H190 C150 80 145 120 105 120 H0 Z" fill="var(--band)"/>
  </svg>

  <h1 class="brand">Verdancy Harbor</h1>

  <div class="name-plate name-plate--1">Name - 1</div>
  <div class="name-plate name-plate--2">Name - 2</div>
  <div class="name-plate name-plate--3">Name - 3</div>

  <div class="about">
    <p>Verdancy Harbor is a state of the art web community that services those progressive professionals who are interested in personal balance and who want to purchase products that are essential to a healthful life.</p>
    <p>Your text goes here. Your text goes here. Your text goes here. Your text goes here. Your text goes here.</p>
  </div>

  <div class="divider"></div>

  <div class="stamp-box">Postage<br>Area</div>

  <div class="address-line address-line--1"></div>
  <div class="address-line address-line--2"></div>
  <div class="address-line address-line--3"></div>
  <div class="address-line address-line--4"></div>
</main>
</body>
</html>
```